NEW Modern Sleek Business Card for VR Language Startup

Our startup is using VR to lead the next wave of world language education. We need a two-sided business card that introduces the larger organization (Brightloom Language Inc) and our contact info on one side and shows the product, Glimwoorld, on the other side.

Side 1 (contact info)= Brightloom Logo and Contact info (name, title, phone, email)

Side 2 (product)= Glimworld logo, text, and website
Text= Culturally Immersive Language Learning Games
Website= www.glimworld-play.com

Target Market(s)

Education, Technology

Contact Information for Business Card

Contact info will be updated upon approval of the design. For now, put this as a placeholder.

Perry Dunmore
Founder & CEO
pdunmore@quillpost-mail.net
(555)-014-2286

Font styles to use
Other font styles liked:
• Gibson and Century Gothic are the brand fonts

Requirements
Nice to have
• I would love to see cohesion between the design and colors of the two logos. I have attached a few business card designs that I like, so you can get a feel for my preferred style.

```html
<!DOCTYPE html>
<html lang="en">
<head>
<meta charset="utf-8">
<title>Glimworld / Brightloom Business Card</title>
<link href="https://fonts.googleapis.com/css2?family=Montserrat:wght@600;700&family=Questrial&display=swap" rel="stylesheet">
<style>
  :root {
    --canvas-bg: #d9d9db;
    --card-black: #0b0b0c;
    --card-charcoal: #262627;
    --band-white: #ffffff;
    --violet: #6b5cf6;
    --cyan: #22d3e6;
    --tag-grey: #5c5c5e;
    --text-white: #f4f4f4;
    --icon-red: #e8344a;
    --ink: #1c1c1e;
  }
  * { margin: 0; padding: 0; box-sizing: border-box; }
  html, body { width: 1200px; height: 1200px; overflow: hidden; }
  body {
    background: var(--canvas-bg);
    font-family: "Questrial", "Century Gothic", sans-serif;
    position: relative;
  }
  .card {
    position: absolute;
    left: 150px;
    width: 900px;
    height: 514px;
    border-radius: 26px;
    overflow: hidden;
    box-shadow: 0 18px 40px rgba(0,0,0,0.25);
  }

  /* Product side */
  .card--product {
    top: 66px;
    background: linear-gradient(120deg, var(--card-black) 0%, #141415 55%, var(--card-charcoal) 100%);
    text-align: center;
  }
  .product-brand {
    position: absolute;
    top: 150px;
    left: 0; right: 0;
    display: flex;
    align-items: center;
    justify-content: center;
    gap: 22px;
  }
  .product-brand__dot {
    width: 46px; height: 46px;
    border-radius: 50%;
    background: linear-gradient(160deg, var(--cyan), var(--violet));
  }
  .product-brand__name {
    font-family: "Questrial", "Century Gothic", sans-serif;
    font-size: 82px;
    color: var(--violet);
    letter-spacing: 1px;
  }
  .product-tagline {
    position: absolute;
    top: 268px;
    left: 0; right: 0;
    font-size: 23px;
    color: var(--tag-grey);
    letter-spacing: 1px;
  }
  .product-url {
    position: absolute;
    top: 372px;
    left: 0; right: 0;
    font-family: "Montserrat", sans-serif;
    font-weight: 700;
    font-size: 22px;
    color: var(--violet);
    letter-spacing: 0.5px;
  }

  /* Contact side */
  .card--contact {
    top: 620px;
    background: linear-gradient(110deg, var(--card-black) 0%, #1a1a1b 45%, var(--card-charcoal) 100%);
  }
  .contact-band {
    position: absolute;
    top: 0; right: 0;
    width: 220px; height: 100%;
    background: var(--band-white);
    display: flex;
    align-items: center;
    justify-content: center;
  }
  .org-brand {
    transform: rotate(-90deg);
    display: flex;
    align-items: center;
    gap: 16px;
    white-space: nowrap;
  }
  .org-brand__dot {
    width: 30px; height: 30px;
    border-radius: 50%;
    background: linear-gradient(135deg, var(--icon-red), var(--violet), var(--cyan));
  }
  .org-brand__name {
    font-family: "Montserrat", sans-serif;
    font-weight: 700;
    font-size: 50px;
    color: var(--ink);
    letter-spacing: 3px;
  }
  .contact-info {
    position: absolute;
    left: 60px;
    bottom: 70px;
    color: var(--text-white);
  }
  .contact-info__name {
    font-family: "Montserrat", sans-serif;
    font-weight: 700;
    font-size: 34px;
    letter-spacing: 1px;
  }
  .contact-info__title {
    font-family: "Questrial", sans-serif;
    font-size: 20px;
    margin-left: 10px;
    letter-spacing: 0.5px;
  }
  .contact-info__lines {
    margin-top: 14px;
    display: flex;
    gap: 30px;
    font-size: 20px;
  }
  .contact-line { display: flex; align-items: center; gap: 10px; }
  .contact-line svg { width: 20px; height: 20px; flex: none; }
</style>
</head>
<body>

<section class="card card--product" aria-label="Product side">
  <div class="product-brand">
    <span class="product-brand__dot"></span>
    <span class="product-brand__name">Glimworld</span>
  </div>
  <p class="product-tagline">Culturally Immersive Language Learning Games</p>
  <p class="product-url">www.glimworld-play.com</p>
</section>

<section class="card card--contact" aria-label="Contact side">
  <div class="contact-info">
    <p><span class="contact-info__name">PERRY DUNMORE</span><span class="contact-info__title">President</span></p>
    <div class="contact-info__lines">
      <span class="contact-line">
        <svg viewBox="0 0 24 24" aria-hidden="true"><path fill="var(--icon-red)" d="M6.6 10.8a15.1 15.1 0 0 0 6.6 6.6l2.2-2.2a1 1 0 0 1 1-.25 11.4 11.4 0 0 0 3.6.57 1 1 0 0 1 1 1V20a1 1 0 0 1-1 1A17 17 0 0 1 3 4a1 1 0 0 1 1-1h3.5a1 1 0 0 1 1 1c0 1.25.2 2.45.57 3.57a1 1 0 0 1-.25 1z"/></svg>
        (555)-014-2286
      </span>
      <span class="contact-line">
        <svg viewBox="0 0 24 24" aria-hidden="true"><rect x="2" y="5" width="20" height="14" rx="2" fill="none" stroke="var(--icon-red)" stroke-width="2"/><path d="M3 6l9 7 9-7" fill="none" stroke="var(--icon-red)" stroke-width="2"/></svg>
        pdunmore@quillpost-mail.net
      </span>
    </div>
  </div>
  <div class="contact-band">
    <div class="org-brand">
      <span class="org-brand__dot"></span>
      <span class="org-brand__name">Brightloom</span>
    </div>
  </div>
</section>

</body>
</html>
```